Presentation Folder, for Cancer Awareness, VERY COLORFULL AND MODERN

This will be a standard size folder that will hold standard 8 1/2 x 11 papers with a business card slot on the flap, this is a very easy project with very little text and the design for the back page is already done so all you really have to do is make a very nice colorful front cover, you will see my attachments are labeled and I gave you alot of instructions, this should be a very fast easy project
Updates

Reason: there has not been enough quality designs, sorry

Target Market(s)

Our Target Market is Dr's that Deal with Cancer patients

Industry/Entity Type

Healthcare

Font styles to use
Serif

Colors

Designer to choose colors to be used in the design.

Requirements
Must have
• Project must be tasteful and look professional with the ribbons as the main focal point in the center of folder the folder should be a nice gray color to accent the color of the ribbons , the back page needs no design it is the" Sorvane Test" in the attachments I sent
Nice to have
• I would like the ribbons displayed in a row, I included a logo sample layout
• a picture on the front of the folder under the words Hereditary Cancer Screening - Then under that put the words - The Power of Knowledge - then add the picture I labeled Great Picture in the attachments

```html
<!DOCTYPE html>
<html lang="en">
<head>
<meta charset="utf-8">
<title>Hereditary Cancer Screening Folder</title>
<link rel="stylesheet" href="https://fonts.googleapis.com/css2?family=Montserrat:wght@600;700&family=Open+Sans:wght@400;600;700&family=Raleway:wght@300;400&display=swap">
<style>
  :root {
    --stage: #e4e4e4;
    --paper: #ffffff;
    --orange: #f26b1d;
    --red: #d9342b;
    --ink: #5e5e5e;
    --ink-soft: #8a8a8a;
    --stripe: #ececec;
    --head-gray: #5b5c5e;
    --lynch: #f6bd2c;
    --pj: #a9c23c;
    --lf: #4aae4b;
    --cowden: #1b8fd8;
    --hdgc: #6b6c6e;
  }
  * { box-sizing: border-box; margin: 0; padding: 0; }
  html, body { width: 1200px; height: 1000px; overflow: hidden; }
  body {
    background: var(--stage);
    display: flex;
    justify-content: center;
    align-items: center;
    gap: 120px;
    font-family: "Open Sans", Arial, sans-serif;
  }
  .panel {
    width: 430px;
    height: 780px;
    background: var(--paper);
    box-shadow: 0 6px 24px rgba(0,0,0,0.12);
    display: flex;
    flex-direction: column;
    align-items: center;
  }

  /* brand lockup */
  .brand { display: flex; flex-direction: column; align-items: center; gap: 8px; }
  .brand-dot { width: 40px; height: 40px; border-radius: 50%; background: var(--orange); }
  .brand-name {
    font-family: "Raleway", Arial, sans-serif;
    font-weight: 400;
    letter-spacing: 5px;
    color: var(--ink);
    text-transform: uppercase;
  }

  /* front cover */
  .front { padding-top: 46px; }
  .front .brand-name { font-size: 21px; }
  .cover-title {
    margin-top: 42px;
    font-family: "Montserrat", Arial, sans-serif;
    font-weight: 600;
    font-size: 23px;
    color: var(--orange);
    letter-spacing: 0.2px;
  }
  .ribbon-row {
    margin-top: 18px;
    width: 388px;
    height: 120px;
    background: linear-gradient(90deg, #f2e23a 0%, #b7b7b7 8%, #ef8fb4 16%, #3fc1c9 24%, #f4a9c9 30%, #9a4fd0 38%, #2f3ec4 45%, #8b5a2b 52%, #f06a9a 58%, #7cbf3a 65%, #1d7fd0 72%, #f5f5f5 78%, #222 84%, #6cc4ef 91%, #7f8ef0 100%);
  }
  .tagline {
    margin-top: 26px;
    font-family: "Raleway", Arial, sans-serif;
    font-weight: 300;
    font-size: 25px;
    letter-spacing: 3.2px;
    color: var(--ink-soft);
  }
  .cover-photo {
    margin-top: 38px;
    width: 430px;
    flex: 1;
    background: linear-gradient(180deg, #eef0ef 0%, #c9b9a4 45%, #8fa2b8 100%);
  }

  /* back page */
  .back { padding: 40px 28px 18px; }
  .menu-title {
    font-family: "Montserrat", Arial, sans-serif;
    font-weight: 600;
    font-size: 27px;
    color: var(--red);
    line-height: 1;
  }
  .menu-title sup { font-size: 10px; vertical-align: top; }
  .menu-sub {
    margin-top: 3px;
    font-family: "Raleway", Arial, sans-serif;
    font-size: 11px;
    letter-spacing: 1.2px;
    color: var(--ink-soft);
  }
  .gene-table {
    margin-top: 12px;
    width: 100%;
    border-collapse: collapse;
    font-size: 7.5px;
    border: 1px solid #cfcfcf;
  }
  .gene-table td, .gene-table th {
    height: 12.6px;
    padding: 0 6px;
    text-align: left;
    white-space: nowrap;
  }
  .gene-table th { color: #fff; font-weight: 700; font-size: 8px; }
  .gene-table .th-gene { background: var(--red); width: 36%; }
  .gene-table .th-organ { background: var(--head-gray); }
  .gene-table tbody tr:nth-child(even) td { background: var(--stripe); }
  .gene { color: var(--red); font-weight: 600; }
  .organ { color: var(--ink); }
  .syndrome td { color: #fff; font-weight: 700; font-size: 8px; letter-spacing: 0.3px; }
  .syndrome.lynch td { background: var(--lynch) !important; }
  .syndrome.pj td { background: var(--pj) !important; }
  .syndrome.lf td { background: var(--lf) !important; }
  .syndrome.cowden td { background: var(--cowden) !important; }
  .syndrome.hdgc td { background: var(--hdgc) !important; }

  .back-footer { margin-top: auto; display: flex; flex-direction: column; align-items: center; }
  .back-footer .brand { flex-direction: row; gap: 12px; }
  .back-footer .brand-dot { width: 34px; height: 34px; }
  .back-footer .brand-name { font-size: 18px; }
  .contact {
    margin-top: 6px;
    font-size: 5.5px;
    color: var(--ink);
    text-align: center;
    line-height: 1.5;
    letter-spacing: 0.4px;
  }
</style>
</head>
<body>

<section class="panel front">
  <div class="brand">
    <span class="brand-dot"></span>
    <span class="brand-name">Meridane Labs</span>
  </div>
  <h1 class="cover-title">HEREDITARY CANCER SCREENING</h1>
  <div class="ribbon-row" role="img" aria-label="Row of colourful cancer awareness ribbons"></div>
  <p class="tagline">The Power of Knowledge</p>
  <div class="cover-photo" role="img" aria-label="Photo of a multi-generation family sharing a meal at an outdoor table"></div>
</section>

<section class="panel back">
  <h2 class="menu-title">Sorvane<sup>™</sup> Test Menu</h2>
  <p class="menu-sub">CLIA# 00D0000000 | MERIDANELABS.EXAMPLE</p>
  <table class="gene-table">
    <thead>
      <tr><th class="th-gene">GENE</th><th class="th-organ">CANCER-ASSOCIATED ORGAN/SYSTEMS</th></tr>
    </thead>
    <tbody>
      <tr><td class="gene">APC</td><td class="organ">Colon</td></tr>
      <tr><td class="gene">ATM</td><td class="organ">Breast/Pancreatic/Brain</td></tr>
      <tr><td class="gene">BARD1</td><td class="organ">Breast/Ovarian</td></tr>
      <tr><td class="gene">BMPR1A</td><td class="organ">Colon</td></tr>
      <tr><td class="gene">BRCA1</td><td class="organ">Breast/Ovarian/Prostate</td></tr>
      <tr><td class="gene">BRCA2</td><td class="organ">Breast/Ovarian/Prostate</td></tr>
      <tr><td class="gene">BRIP1</td><td class="organ">Breast/Ovarian</td></tr>
      <tr><td class="gene">CDK4</td><td class="organ">Melanoma</td></tr>
      <tr><td class="gene">P16 (CDKN2A)</td><td class="organ">Melanoma/Breast/Pancreatic/Squamous</td></tr>
      <tr><td class="gene">FANCC</td><td class="organ">Blood</td></tr>
      <tr><td class="gene">MEN1</td><td class="organ">Thyroid/Parathyroid</td></tr>
      <tr><td class="gene">MET</td><td class="organ">Renal/Hepatic</td></tr>
      <tr><td class="gene">MRE11A</td><td class="organ">Ovarian/Breast</td></tr>
      <tr><td class="gene">NBN</td><td class="organ">Breast/Ovarian/Prostate/Melanoma</td></tr>
      <tr><td class="gene">NF1</td><td class="organ">Blood</td></tr>
      <tr><td class="gene">NTRK1</td><td class="organ">Thyroid/Parathyroid</td></tr>
      <tr><td class="gene">PALB2</td><td class="organ">Breast/Ovarian/Pancreatic</td></tr>
      <tr><td class="gene">PTCH1</td><td class="organ">Melanoma/Brain/Breast/Colon</td></tr>
      <tr><td class="gene">RAD50</td><td class="organ">Breast/Ovarian</td></tr>
      <tr><td class="gene">RAD51C</td><td class="organ">Ovarian/Breast</td></tr>
      <tr><td class="gene">RAD51D</td><td class="organ">Ovarian/Breast</td></tr>
      <tr><td class="gene">RET</td><td class="organ">Lung/Thyroid/Parathyroid</td></tr>
      <tr><td class="gene">SMAD4</td><td class="organ">Colon/Pancreas</td></tr>
      <tr class="syndrome lynch"><td colspan="2">LYNCH SYNDROME GENES</td></tr>
      <tr><td class="gene">MLH1</td><td class="organ">Colorectal/Ovarian</td></tr>
      <tr><td class="gene">MSH2</td><td class="organ">Colorectal/Ovarian</td></tr>
      <tr><td class="gene">MSH6</td><td class="organ">Colorectal/Ovarian</td></tr>
      <tr><td class="gene">PMS2</td><td class="organ">Colorectal/Ovarian</td></tr>
      <tr><td class="gene">EPCAM</td><td class="organ">Colorectal</td></tr>
      <tr class="syndrome pj"><td colspan="2">PEUTZ-JEGHERS SYNDROME GENE</td></tr>
      <tr><td class="gene">STK11</td><td class="organ">Breast/Ovarian/Melanoma/Colorectal/Lung</td></tr>
      <tr class="syndrome lf"><td colspan="2">LI-FRAUMENI SYNDROME GENE</td></tr>
      <tr><td class="gene">CHEK2</td><td class="organ">Breast/Ovarian/Prostate</td></tr>
      <tr><td class="gene">TP53</td><td class="organ">Breast/Bladder/Ovarian/Squamous</td></tr>
      <tr class="syndrome cowden"><td colspan="2">COWDEN SYNDROME GENE</td></tr>
      <tr><td class="gene">PTEN</td><td class="organ">Endometrium/Breast/Prostate/Lung</td></tr>
      <tr class="syndrome hdgc"><td colspan="2">HEREDITARY DIFFUSE GASTRIC CANCER SYNDROME GENE</td></tr>
      <tr><td class="gene">CDH1</td><td class="organ">Breast/Gastric/Ovarian/Prostate</td></tr>
      <tr><td class="gene">VHL</td><td class="organ">Renal</td></tr>
    </tbody>
  </table>
  <footer class="back-footer">
    <div class="brand">
      <span class="brand-dot"></span>
      <span class="brand-name">Meridane Labs</span>
    </div>
    <p class="contact">220 HARBOR RIDGE WAY | SUITE B | FAIRVIEW, GA 30000<br>(tel) 555.010.2200 | (fax) 555.010.2201 | info@meridanelabs.example</p>
  </footer>
</section>

</body>
</html>
```